BrivoTerna. Lantern of the Steady Harvest. Business card

Professional business card for BrivoTerna (Lantern of the Steady Harvest)
My rationale: Strategy-> Execution-> Results-> Value that lead to the BrivoTerna name: We put the Lantern of the Steady Harvest.
We deliver value to our customers helping them at defining a good strategy (cyan arrow). 90% of well formulated strategies fail due to poor execution so we also consider strategical execution very important (green arrow). Due to the execution we obtain the results (blue arrow). Finally, the results provide feedback to redefine strategy, and the new strategy has to be executed and new results obtained providing new feedback and on and on. It's like a wheel that finally, must create corporate value: value for shareholders, staholders, employees, providers...-

Target Market(s)

CEOs and steering comitees , invewrnent funds

Industry/Entity Type

Business Consultant

Contact Information for Business Card

Teodoro Vinsquel
CEO & Founder
teodoro.vinsquel@brivoterna-example.com
Mobile: +34 655.803.912
www.brivoterna-example.com

Colors

Designer to choose colors to be used in the design.

Requirements
Nice to have
• Nice to hace the words: Strategy, execution, results
• Nice to vave the claim: Lantern of the Steady Harvest
• The three colors should be shown:
• cyan for STRATEGY
• green for EXECUTION
• blue for RESULTS
Should not have
• Complete black background

```html
<!DOCTYPE html>
<html lang="en">
<head>
<meta charset="utf-8">
<title>BrivoTerna – Business Card</title>
<link href="https://fonts.googleapis.com/css2?family=Roboto:wght@300;400;500;700&family=Roboto+Condensed:wght@700&display=swap" rel="stylesheet">
<style>
  :root {
    --backdrop: #9d9d9f;
    --brand-blue: #00309a;
    --brand-blue-deep: #062a78;
    --brand-blue-light: #0b55d0;
    --brand-cyan: #00a6e6;
    --ink-blue: #1f3f9f;
    --paper: #ffffff;
    --wash-blue: #e4e8f4;
    --wash-green: #f2f7e6;
    --wash-cyan: #e3f4fb;
  }
  * { margin: 0; padding: 0; box-sizing: border-box; }
  html, body {
    width: 1200px; height: 900px; overflow: hidden;
    background: var(--backdrop);
    font-family: "Roboto", Arial, sans-serif;
  }
  .canvas { position: relative; width: 1200px; height: 900px; }

  .card {
    position: absolute;
    left: 363px;
    width: 475px;
    height: 271px;
    overflow: hidden;
  }
  .card--front { top: 145px; background: var(--brand-blue); }
  .card--back { top: 484px; background: var(--paper); }

  .decor {
    position: absolute;
  }
  .decor--front {
    left: 0; top: 0; width: 272px; height: 271px;
    background: radial-gradient(ellipse 70% 60% at 35% 70%, var(--brand-blue-light) 0%, var(--brand-blue-deep) 55%, rgba(0,48,154,0) 100%);
  }
  .decor--back {
    left: 212px; top: 0; width: 263px; height: 262px;
    background:
      radial-gradient(ellipse 55% 30% at 60% 85%, var(--wash-cyan) 0%, rgba(227,244,251,0) 100%),
      radial-gradient(ellipse 60% 30% at 60% 62%, var(--wash-green) 0%, rgba(242,247,230,0) 100%),
      radial-gradient(ellipse 65% 45% at 65% 35%, var(--wash-blue) 0%, rgba(228,232,244,0) 100%);
  }

  .brand-square {
    position: absolute;
    left: 78px; top: 26px;
    width: 46px; height: 46px;
    background: var(--brand-blue);
  }

  .wordmark {
    position: absolute;
    font-family: "Roboto Condensed", "Roboto", Arial, sans-serif;
    font-weight: 700;
    letter-spacing: -0.5px;
    line-height: 1;
    white-space: nowrap;
  }
  .card--front .wordmark {
    right: 27px; top: 203px;
    font-size: 42px;
    color: var(--paper);
  }
  .card--back .wordmark {
    left: 26px; top: 88px;
    font-size: 35px;
    color: var(--brand-blue);
  }

  .holder { position: absolute; left: 26px; top: 143px; }
  .holder__name {
    font-size: 17px; font-weight: 700;
    color: var(--brand-cyan); line-height: 1.1;
  }
  .holder__role {
    font-size: 12px; font-weight: 300;
    color: var(--ink-blue); line-height: 1.2;
  }

  .contacts {
    position: absolute; left: 26px; top: 189px;
    list-style: none;
  }
  .contacts__item {
    display: flex; align-items: center; gap: 5px;
    font-size: 12px; font-weight: 300;
    color: var(--ink-blue);
    height: 18px;
  }
  .contacts__icon { width: 9px; height: 9px; flex: none; }

  .footer-band {
    position: absolute; left: 0; bottom: 0;
    width: 100%; height: 9px;
  }
  .footer-band__cyan {
    position: absolute; left: 0; top: 0;
    width: 49px; height: 9px; background: var(--brand-cyan);
  }
  .footer-band__blue {
    position: absolute; left: 53px; right: 0; top: 0;
    height: 9px; background: var(--brand-blue);
  }
</style>
</head>
<body>
<main class="canvas">

  <section class="card card--front" aria-label="Business card front">
    <div class="decor decor--front" role="img" aria-label="Large brand symbol decoration in deep blue tones"></div>
    <p class="wordmark">BrivoTerna</p>
  </section>

  <section class="card card--back" aria-label="Business card back">
    <div class="decor decor--back" role="img" aria-label="Faint brand symbol decoration in pale blue, green and cyan"></div>

    <span class="brand-square" aria-hidden="true"></span>
    <p class="wordmark">BrivoTerna</p>

    <div class="holder">
      <p class="holder__name">Teodoro Vinsquel</p>
      <p class="holder__role">CEO &amp; Founder</p>
    </div>

    <ul class="contacts">
      <li class="contacts__item">
        <svg class="contacts__icon" viewBox="0 0 10 10" aria-hidden="true">
          <path d="M2 0.6 L3.6 2.6 L2.8 3.6 Q4 6 6.4 7.2 L7.4 6.4 L9.4 8 L8.4 9.4 Q4.6 9.4 2 6.8 Q0.4 4.6 0.6 1.6 Z" fill="var(--brand-cyan)"/>
        </svg>
        +34 655.803.912
      </li>
      <li class="contacts__item">
        <svg class="contacts__icon" viewBox="0 0 10 10" aria-hidden="true">
          <circle cx="5" cy="5" r="4.5" fill="var(--brand-cyan)"/>
          <path d="M0.5 5 H9.5 M5 0.5 Q2.4 5 5 9.5 M5 0.5 Q7.6 5 5 9.5" stroke="#fff" stroke-width="0.8" fill="none"/>
        </svg>
        www.brivoterna-example.com
      </li>
      <li class="contacts__item">
        <svg class="contacts__icon" viewBox="0 0 10 10" aria-hidden="true">
          <rect x="0.3" y="2" width="9.4" height="6.4" fill="var(--brand-cyan)"/>
          <path d="M0.5 2.3 L5 5.8 L9.5 2.3" stroke="#fff" stroke-width="0.8" fill="none"/>
        </svg>
        teodoro.vinsquel@brivoterna-example.com
      </li>
    </ul>

    <div class="footer-band" aria-hidden="true">
      <span class="footer-band__cyan"></span>
      <span class="footer-band__blue"></span>
    </div>
  </section>

</main>
</body>
</html>
```